Business Card Design for Marketing Firm

Looking for business card design for higher end marketing firm. Clean but impressionable/trendy. We are a marketing firm that represents manufacturers in the foodservice equipment and supply industry. Our customers are end users such has hotels, restaurants, country clubs, convention centers and casinos as well as distributors of restaurants supplies and equipment, and manufacturers of foodservice equipment and supplies.
Target Market(s)
Hotels, Restaurants, Supply & Equipment Distributors, Foodservice Manufacturers
Industry/Entity Type
Foodservice/Hospitality
Contact Information for Business Card
Name, Title, Contact Number, Email, Website, Social Media, Address
Requirements
Must have
- Clean & Simple but Serious and Impressionable

```html
<!DOCTYPE html>
<html lang="en">
<head>
<meta charset="utf-8">
<title>Meridian Hospitality Reps – Business Card</title>
<link href="https://fonts.googleapis.com/css2?family=Cinzel:wght@400;700&family=Arimo:wght@400&display=swap" rel="stylesheet">
<style>
  :root {
    --navy: #00006e;
    --paper: #f6f6f8;
    --ink: #1f1f24;
    --muted: #5b5b63;
    --backdrop: #7b7b7b;
    --white: #ffffff;
  }
  * { box-sizing: border-box; margin: 0; padding: 0; }
  html, body { width: 1200px; height: 900px; overflow: hidden; }
  body {
    background: var(--backdrop);
    display: flex;
    flex-direction: column;
    align-items: center;
    justify-content: center;
    gap: 56px;
    font-family: "Arimo", Arial, sans-serif;
  }
  .card {
    width: 560px;
    height: 320px;
    border-radius: 22px;
    position: relative;
    box-shadow: 0 10px 24px rgba(0,0,0,0.28);
  }
  .card--front { background: var(--navy); color: var(--white); }
  .card--back { background: var(--paper); color: var(--navy); }

  .brand {
    position: absolute;
    display: flex;
    flex-direction: column;
    align-items: center;
    font-family: "Cinzel", Georgia, serif;
    font-weight: 400;
  }
  .brand__mark {
    width: 44px; height: 44px;
    border-radius: 50%;
    border: 2px solid currentColor;
    margin-bottom: 14px;
  }
  .brand__name { font-size: 26px; letter-spacing: 0.5px; line-height: 1; }
  .brand__sub { align-self: flex-end; font-size: 15px; letter-spacing: 1px; margin-top: 2px; }
  .brand__rule { width: 100%; height: 1.5px; background: currentColor; margin-top: 4px; }

  .card--front .brand { left: 50%; top: 70px; transform: translateX(-50%); }
  .front__web {
    position: absolute; left: 0; right: 0; top: 236px;
    text-align: center; font-size: 13px; letter-spacing: 3px;
  }

  .card--back .brand { left: 50%; top: 28px; transform: translateX(-50%); }
  .card--back .brand__name { font-size: 22px; }
  .card--back .brand__sub { font-size: 13px; }
  .card--back .brand__mark { width: 36px; height: 36px; margin-bottom: 10px; }

  .social { position: absolute; top: 18px; right: 22px; display: flex; gap: 5px; }
  .social__dot { width: 18px; height: 18px; border-radius: 50%; background: var(--navy); }

  .person {
    position: absolute; right: 300px; top: 190px; text-align: right;
  }
  .person__name {
    font-family: "Cinzel", Georgia, serif; font-weight: 700;
    font-size: 26px; color: var(--navy); line-height: 1;
  }
  .person__title { font-size: 15px; color: var(--muted); margin-top: 4px; }

  .divider {
    position: absolute; left: 282px; top: 170px;
    width: 1px; height: 104px; background: var(--muted);
  }
  .contact {
    position: absolute; left: 300px; top: 168px;
    font-size: 14px; color: var(--ink); line-height: 1.35;
  }
  .contact__address { margin-bottom: 10px; }
  .contact__list { list-style: none; }
  .contact__item { display: flex; align-items: center; gap: 8px; }
  .contact__icon { width: 12px; height: 12px; fill: var(--navy); flex: none; }
</style>
</head>
<body>

  <section class="card card--front" aria-label="Card front">
    <div class="brand">
      <span class="brand__mark" aria-hidden="true"></span>
      <span class="brand__name">MERIDIAN HOSPITALITY</span>
      <span class="brand__sub">REPS</span>
      <span class="brand__rule"></span>
    </div>
    <p class="front__web">www.MERIDIAN.com</p>
  </section>

  <section class="card card--back" aria-label="Card back">
    <div class="social" aria-label="Social media">
      <span class="social__dot"></span>
      <span class="social__dot"></span>
      <span class="social__dot"></span>
    </div>

    <div class="brand">
      <span class="brand__mark" aria-hidden="true"></span>
      <span class="brand__name">MERIDIAN HOSPITALITY</span>
      <span class="brand__sub">REPS</span>
      <span class="brand__rule"></span>
    </div>

    <div class="person">
      <p class="person__name">THOMAS REED</p>
      <p class="person__title">President</p>
    </div>

    <span class="divider"></span>

    <div class="contact">
      <p class="contact__address">2716 Harbor View Lane<br>Glen Ridge, NY 10540</p>
      <ul class="contact__list">
        <li class="contact__item">
          <svg class="contact__icon" viewBox="0 0 24 24" aria-hidden="true"><path d="M6.6 10.8a15.2 15.2 0 0 0 6.6 6.6l2.2-2.2a1 1 0 0 1 1-.25 11.4 11.4 0 0 0 3.6.57 1 1 0 0 1 1 1V20a1 1 0 0 1-1 1A17 17 0 0 1 3 4a1 1 0 0 1 1-1h3.5a1 1 0 0 1 1 1c0 1.25.2 2.45.57 3.57a1 1 0 0 1-.25 1z"/></svg>
          (555) 0142-7781
        </li>
        <li class="contact__item">
          <svg class="contact__icon" viewBox="0 0 24 24" aria-hidden="true"><path d="M2 5h20v14H2z M3 6l9 7 9-7" fill="none" stroke="#00006e" stroke-width="2.5"/></svg>
          name@MERIDIAN.com
        </li>
        <li class="contact__item">
          <svg class="contact__icon" viewBox="0 0 24 24" aria-hidden="true"><circle cx="12" cy="12" r="10" fill="none" stroke="#00006e" stroke-width="2.5"/><path d="M2 12h20M12 2c3 3.5 3 16.5 0 20M12 2c-3 3.5-3 16.5 0 20" fill="none" stroke="#00006e" stroke-width="2"/></svg>
          www.MERIDIAN.com
        </li>
      </ul>
    </div>
  </section>

</body>
</html>
```